Business Card Design

We custom build & and install Air filtration systems for mining machines - the system filters the air going into the cabin to protect the operator/driver Examples of the machines we install our units to would be Ironhaven or Veltoro. Australian owned company Our company colors are sky blue with polished Stainless steel lettering & framing. I have a logo which I will upload but I would like the new image to be crisper.

Industry/Entity Type

Business

Contact Information for Business Card

Company name - Clearlung Pty Ltd
Dale Morrissey - Position - Sales & Product Development Contact numbers Mob 0428 359 162 Tel - 07 3581 4296
Address - 147 Quarrel Rd, Wendlebury, Brisbane 4108, Australia

Colors
0255a3

Requirements
Must have
• sky blue & polished chrome lettering

```html
<!DOCTYPE html>
<html lang="en">
<head>
<meta charset="utf-8">
<title>Clearlung Business Card</title>
<link href="https://fonts.googleapis.com/css2?family=Exo+2:wght@400;500;700&family=Arimo:wght@400&display=swap" rel="stylesheet">
<style>
  :root {
    --page: #e6e7e9;
    --card-white: #ffffff;
    --card-grey: #e4e5e7;
    --brand-blue: #22409a;
    --ink-white: #ffffff;
    --ink-dark: #3a3b3d;
    --ink-mid: #5a5b5e;
  }
  html, body {
    margin: 0;
    width: 1200px;
    height: 1085px;
    overflow: hidden;
    background: var(--page);
  }
  .card {
    position: absolute;
    left: 100px;
    top: 252px;
    width: 1000px;
    height: 580px;
    background: linear-gradient(160deg, var(--card-white) 0%, var(--card-white) 45%, var(--card-grey) 100%);
    box-shadow: 0 10px 30px rgba(0,0,0,0.18);
    overflow: hidden;
  }
  .contact-panel {
    position: absolute;
    left: 0;
    top: 0;
    width: 1000px;
    height: 580px;
  }
  .contact-panel .panel-fill { fill: var(--brand-blue); }
  .contact-panel .icon-ring { fill: none; stroke: var(--ink-white); stroke-width: 3; }
  .contact-panel .icon-glyph { fill: var(--ink-white); }
  .contact-panel .icon-hole { fill: var(--brand-blue); }
  .contact-panel .icon-line { fill: none; stroke: var(--ink-white); stroke-width: 2.2; }
  .contact-block {
    position: absolute;
    right: 628px;
    margin: 0;
    font-family: "Exo 2", sans-serif;
    font-weight: 400;
    font-size: 29px;
    line-height: 36px;
    color: var(--ink-white);
    text-align: right;
    letter-spacing: 0.5px;
  }
  .contact-phone { top: 80px; }
  .contact-address { top: 200px; }
  .contact-web { top: 384px; }
  .brand {
    position: absolute;
    right: 70px;
    top: 64px;
    display: flex;
    align-items: center;
    gap: 16px;
  }
  .brand-square {
    width: 40px;
    height: 40px;
    background: var(--brand-blue);
  }
  .brand-name {
    font-family: "Exo 2", sans-serif;
    font-weight: 700;
    font-size: 62px;
    line-height: 1;
    color: var(--brand-blue);
  }
  .person {
    position: absolute;
    right: 70px;
    top: 300px;
    text-align: right;
    font-family: "Arimo", sans-serif;
  }
  .person-name {
    margin: 0;
    font-size: 38px;
    letter-spacing: 1.5px;
    color: var(--ink-dark);
  }
  .person-role {
    margin: 6px 0 0;
    font-size: 30px;
    color: var(--ink-mid);
  }
</style>
</head>
<body>
  <main class="card">
    <svg class="contact-panel" viewBox="0 0 1000 580" aria-hidden="true">
      <path class="panel-fill" d="M0 0 H400 V84 C400 98 408 98 420 98 A52 52 0 0 1 420 202 C408 202 400 202 400 216 V224 C400 238 408 238 420 238 A52 52 0 0 1 420 342 C408 342 400 342 400 356 V364 C400 378 408 378 420 378 A52 52 0 0 1 420 482 C408 482 400 482 400 496 V580 H0 Z"/>
      <g class="icon icon-phone" transform="translate(-14 0)">
        <circle class="icon-ring" cx="440" cy="150" r="23"/>
        <path class="icon-glyph" transform="translate(440 150) scale(0.85) translate(-445 -150)" d="M430 137 l6 -3 l5 9 l-4 3 c2 5 5 8 9 10 l3 -4 l9 5 l-3 6 c-12 1 -27 -13 -25 -26 z"/>
      </g>
      <g class="icon icon-pin" transform="translate(-14 0)">
        <circle class="icon-ring" cx="440" cy="290" r="23"/>
        <path class="icon-glyph" d="M440 276 a10 10 0 0 1 10 10 c0 7 -10 18 -10 18 c0 0 -10 -11 -10 -18 a10 10 0 0 1 10 -10 z"/>
        <circle class="icon-hole" cx="440" cy="286" r="3.5"/>
      </g>
      <g class="icon icon-globe" transform="translate(-14 0)">
        <circle class="icon-ring" cx="440" cy="430" r="23"/>
        <circle class="icon-line" cx="440" cy="430" r="13"/>
        <ellipse class="icon-line" cx="440" cy="430" rx="5" ry="13"/>
        <line class="icon-line" x1="427" y1="430" x2="453" y2="430"/>
        <line class="icon-line" x1="429" y1="423" x2="451" y2="423"/>
        <line class="icon-line" x1="429" y1="437" x2="451" y2="437"/>
      </g>
    </svg>

    <p class="contact-block contact-phone">013 579 2468<br>013 579 2468</p>
    <p class="contact-block contact-address">054.12th floor,<br>Parkview Lane Road<br>NRB</p>
    <p class="contact-block contact-web">myname@mailbox.com<br>mysitename.com</p>

    <div class="brand">
      <span class="brand-square"></span>
      <span class="brand-name">Clearlung</span>
    </div>

    <div class="person">
      <p class="person-name">OWEN HARTLEY</p>
      <p class="person-role">Managing Director</p>
    </div>
  </main>
</body>
</html>
```